Business Card Re-Design/Update

We'd like to update out business cards. I've included our current "Style guide" which has the colour scheme of the organisation in it. I've also included the branding files with logos etc in them.

I've also included a copy of one of our existing cards so that you can see how ugly/dated they look. I'd like a fresh modern corporate look.

Target Market(s)

These are for our clients, potential clients, industry contacts - like all business cards

Contact Information for Business Card

Name
Position
Company Address - Level 1, 47 Fernby Street, Carlow Qld 4072
Direct Phone
mobile
Email
Website -www.korvalit.com.au
Logo

Colors

Designer to choose colors to be used in the design.

Requirements
Must have
• Main Logo
• Cards will need to be editable to be able to personalize them for each new employee.
Nice to have
• The MapOut, ShipWell, KeepSteady would be okay to have if they can be sensibly and professionally added to the look without detracting from the main imagery.
• Maybe they could go on the back of the card? will leave this to your creative discretion as to whether/where they fit.
Should not have
• Should not have decorative or script fonts

```html
<!DOCTYPE html>
<html lang="en">
<head>
<meta charset="utf-8">
<title>korvalIT business card</title>
<link rel="stylesheet" href="https://fonts.googleapis.com/css2?family=Arimo:wght@400;700&display=swap">
<style>
  :root {
    --backdrop: #e4e4e4;
    --card-white: #f7f7f7;
    --brand-red: #c8161d;
    --brand-red-deep: #a30c12;
    --ink: #1c1c1c;
    --ink-soft: #555555;
    --rule: #9a1a1e;
    --on-red: #ffffff;
  }
  * { box-sizing: border-box; margin: 0; padding: 0; }
  html, body { width: 1200px; height: 960px; overflow: hidden; }
  body {
    background: var(--backdrop);
    font-family: "Arimo", Arial, sans-serif;
    position: relative;
  }
  .card {
    position: absolute;
    width: 600px;
    height: 343px;
    overflow: hidden;
  }
  /* Front */
  .card-front {
    left: 314px; top: 113px;
    background: var(--card-white);
  }
  .brand-mark {
    position: absolute;
    right: 42px; top: 44px;
    display: flex; align-items: center; gap: 10px;
    color: var(--brand-red);
    font-weight: 700;
    font-size: 30px;
    letter-spacing: -0.5px;
  }
  .brand-square {
    width: 34px; height: 34px;
    background: var(--brand-red);
  }
  .person-name {
    position: absolute; left: 42px; top: 152px;
    color: var(--brand-red-deep);
    font-weight: 700; font-size: 20px;
    letter-spacing: -0.2px;
  }
  .person-role {
    position: absolute; left: 43px; top: 176px;
    color: var(--ink); font-size: 14px;
  }
  .divider {
    position: absolute; left: 42px; top: 207px;
    width: 516px; height: 1px; background: var(--rule);
  }
  .contact-col {
    position: absolute; top: 228px;
    list-style: none;
    color: var(--ink-soft); font-size: 14px;
  }
  .contact-col li {
    display: flex; align-items: center; gap: 5px;
    height: 19px;
  }
  .contact-col svg { width: 12px; height: 12px; fill: var(--brand-red); flex: none; }
  .contact-col.left { left: 42px; }
  .contact-col.right { left: 226px; }
  .address {
    position: absolute; left: 42px; top: 297px;
    color: var(--ink-soft); font-size: 14px;
  }
  /* Back */
  .card-back {
    left: 311px; top: 472px;
    background: linear-gradient(180deg, var(--brand-red) 0%, var(--brand-red-deep) 100%);
    color: var(--on-red);
  }
  .back-decoration {
    position: absolute; left: 330px; top: 60px;
    width: 300px; height: 300px;
    background: rgba(255,255,255,0.06);
  }
  .back-brand {
    position: absolute; left: 0; right: 0; top: 132px;
    display: flex; justify-content: center; align-items: center; gap: 16px;
    font-weight: 700; font-size: 50px; letter-spacing: -1px;
  }
  .back-brand .brand-square { width: 56px; height: 56px; background: var(--on-red); }
  .service-list {
    position: absolute; left: 0; right: 0; top: 278px;
    display: flex; justify-content: center; gap: 34px;
    list-style: none;
  }
  .service {
    display: flex; align-items: center; gap: 6px;
    font-weight: 700; font-size: 25px; letter-spacing: -0.4px;
  }
  .service-square { width: 22px; height: 22px; background: var(--on-red); }
</style>
</head>
<body>

<section class="card card-front" aria-label="Card front">
  <div class="brand-mark"><span class="brand-square"></span>korvalIT</div>

  <h1 class="person-name">MAREN HOLT</h1>
  <p class="person-role">Business Development Manager</p>
  <div class="divider"></div>

  <ul class="contact-col left">
    <li><svg viewBox="0 0 12 12"><path d="M2.5 0.5l2 2-1 1.5c.8 1.6 1.9 2.7 3.5 3.5l1.5-1 2 2-1.5 2C4.5 10 1.5 7 .5 2z"/></svg>+61 (0)7 5550 1840</li>
    <li><svg viewBox="0 0 12 12"><path d="M2.5 0.5l2 2-1 1.5c.8 1.6 1.9 2.7 3.5 3.5l1.5-1 2 2-1.5 2C4.5 10 1.5 7 .5 2z"/></svg>+61 (0)7 5550 1846</li>
    <li><svg viewBox="0 0 12 12"><path d="M3 0h6a1 1 0 0 1 1 1v10a1 1 0 0 1-1 1H3a1 1 0 0 1-1-1V1a1 1 0 0 1 1-1zm.5 1.5v7.5h5V1.5z"/></svg>+61 (0)400 555 219</li>
  </ul>

  <ul class="contact-col right">
    <li><svg viewBox="0 0 12 12"><path d="M3 0h6v3H3zM0 4h12v5h-2v3H2V9H0zm3 4v3h6V8z"/></svg>+61 (0)7 5550 1849</li>
    <li><svg viewBox="0 0 12 12"><path d="M0 2h12v1L6 7 0 3zm0 2.5l6 4 6-4V10H0z"/></svg>mholt@korvalit.com.au</li>
    <li><svg viewBox="0 0 12 12"><circle cx="6" cy="6" r="6"/></svg>www.korvalit.com.au</li>
  </ul>

  <p class="address">Level 1, 47 Fernby Street, Carlow Qld 4072</p>
</section>

<section class="card card-back" aria-label="Card back">
  <div class="back-decoration"></div>
  <div class="back-brand"><span class="brand-square"></span>korvalIT</div>
  <ul class="service-list">
    <li class="service"><span class="service-square"></span>MapOut</li>
    <li class="service"><span class="service-square"></span>ShipWell</li>
    <li class="service"><span class="service-square"></span>KeepSteady</li>
  </ul>
</section>

</body>
</html>
```